KRV Boltmaster Manufacturer New Web Design

We need a new theme designed for metal fastener manufacturing company, KRV Boltmaster Group, a $60M division of Marrowfield Forge Holdings, Inc. We manufacture screw, pins and washers to industrial customers (non-Automotive) such as HN Homeware, Paul Brenner, LUX, Venmora, etc. Our current website is www.boltmaster.example. We would like to stick with the same logo/color scheme, however, I'm aiming to modernize the website's look and feel.

Here are some of our competitor's websites:
- https://www.torvalink.example/
- http://glenrivet.example/
- http://www.harlowbuiltjoining.example/
- http://lugsandcustoms.example/
- http://www.dunmerebolt.example/

Target Market(s)

We primarily want to target engineers working in the following markets:
- Appliance (HN Homeware, Frostavel)
- Ag (Brenner, LUX)
- Recreational Vehicle (Venmora, Tundra Fox)
- Outdoor Power (Brellvik, Pask)

We secondarily want to target buyers working at the above markets as well as buyers at Fastener distributors such as Boltique, Parts Dynamics, Kessel Fordham.

Industry/Entity Type

Metal Forging

Number of Pages Required

1 page

Requirements
Must have
• For products: "Threaded" product as the primary focus. "Pins" product is the secondary focus, followed by all others.
• Please use same logo and color scheme as I do not plan to change.
Nice to have
• Highlight our featured proprietary products (pamphlets attached). KRV Boltmaster's GRIP-N, KelDrive, Boltmaster Coil, Avalanche.

```html
<!DOCTYPE html>
<html lang="en">
<head>
<meta charset="utf-8">
<title>KRV Boltmaster Group</title>
<link rel="stylesheet" href="https://fonts.googleapis.com/css2?family=Roboto+Condensed:ital,wght@0,400;0,700;1,300;1,400;1,700&display=swap">
<style>
:root{
  --blue:#2a8fd3;
  --teal:#1aa98a;
  --nav:#231f20;
  --ink:#222;
  --muted:#555;
  --footer:#000;
  --base:#1e1e1e;
  --white:#fff;
}
*{box-sizing:border-box;margin:0;padding:0}
html,body{width:1200px;height:2344px;overflow:hidden}
body{font-family:"Roboto Condensed",Arial,sans-serif;font-style:italic;color:var(--ink);background:var(--white);position:relative}
.wrap{position:relative;width:1028px;margin:0 auto;height:100%}
a{color:inherit;text-decoration:none}

.site-header{height:86px}
.brand{position:absolute;left:0;top:14px;display:flex;align-items:center;gap:10px}
.brand-mark{width:58px;height:58px;border-radius:50%;background:var(--blue)}
.brand-name{font-size:34px;color:var(--blue);font-weight:400;letter-spacing:-.5px;white-space:nowrap}
.top-contact{position:absolute;right:0;top:32px;display:flex;gap:38px;font-size:16px;color:var(--blue);white-space:nowrap}
.top-contact span{display:flex;align-items:center;gap:10px}

.main-nav{height:52px;background:var(--nav)}
.main-nav ul{list-style:none;display:flex;justify-content:space-between;height:52px}
.main-nav li{display:flex;align-items:center;justify-content:center;padding:0 6px;color:var(--white);font-size:16px;text-transform:uppercase;white-space:nowrap}
.main-nav li.active{background:var(--teal);width:84px}
.main-nav li.quote{background:var(--blue);width:154px}

.hero{height:480px;position:relative;background:linear-gradient(180deg,#5d8fd6 0%,#a9c6ea 45%,#c9a06b 78%,#8b5a34 100%)}
.hero-caption{position:absolute;left:652px;top:145px;width:462px;height:187px;background:rgba(35,35,45,.85);color:var(--white);font-size:44px;line-height:56px;text-transform:uppercase;display:flex;flex-direction:column;justify-content:center;padding-left:32px;white-space:nowrap}
.hero-dots{position:absolute;left:1149px;top:196px;display:flex;flex-direction:column;gap:5px}
.hero-dots i{width:14px;height:14px;border-radius:50%;border:2px solid var(--white)}
.hero-dots i.on{background:#222;border-color:#222}

.section-title{text-align:center;color:var(--blue);font-size:33px;font-weight:400;text-transform:uppercase}
.products{height:580px;padding-top:62px}
.product-grid{display:flex;gap:11px;margin-top:32px}
.product{width:248px}
.product-photo{height:218px}
.product h3{font-size:22px;font-weight:400;margin-top:20px;text-transform:uppercase}
.product p{font-size:13px;line-height:20px;color:var(--muted);margin-top:14px}
.product .more{display:block;font-size:13px;margin-top:18px}

.about{height:458px;background:var(--teal);color:var(--white)}
.about h2{position:absolute;left:0;top:58px;font-size:37px;font-weight:400;line-height:44px;text-transform:uppercase}
.about p{position:absolute;left:0;top:153px;width:470px;font-size:16.5px;line-height:24.5px}
.about .btn{position:absolute;left:0;top:349px;width:136px;height:45px;background:var(--blue);display:flex;align-items:center;justify-content:center;font-size:16px}
.about-video{position:absolute;left:544px;top:85px;width:486px;height:290px;background:linear-gradient(180deg,#111 0 6%,#e8ecef 6%,#cfd6dc 88%,#111 88%)}

.customers{height:330px;padding-top:62px}
.logo-row{position:relative;height:60px;margin-top:80px}
.partner{position:absolute;top:0;transform:translateX(-50%);display:flex;align-items:center;gap:10px;font-size:22px;font-weight:700;font-style:normal;color:var(--ink);white-space:nowrap}
.partner i{width:30px;height:30px;border-radius:50%;background:#1c3c6e}

.site-footer{height:298px;background:var(--footer);color:var(--white)}
.foot-brand{position:absolute;left:0;top:46px;display:flex;align-items:center;gap:8px}
.foot-brand .brand-mark{width:46px;height:46px}
.foot-brand .brand-name{font-size:25px}
.social{position:absolute;left:8px;top:147px;display:flex;gap:18px}
.social i{width:14px;height:14px;border-radius:50%;background:var(--white)}
.foot-col h4{font-size:17px;font-weight:300;color:#ccc}
.foot-contact{position:absolute;left:294px;top:52px}
.foot-contact div{display:flex;align-items:center;gap:18px;font-size:16px;color:#ccc;margin-top:22px;white-space:nowrap}
.foot-links{position:absolute;left:584px;top:52px}
.foot-links ul{list-style:none;margin-top:14px}
.foot-links li{font-size:12px;line-height:24.5px;color:#ccc}
.foot-links li::before{content:"> ";}
.newsletter{position:absolute;left:750px;top:50px}
.newsletter .field{width:272px;height:52px;border:1.5px solid #ccc;margin-top:16px;padding-left:26px;display:flex;align-items:center;font-size:13px;font-style:normal;color:#aaa}
.newsletter .submit{width:194px;height:48px;background:var(--blue);margin-top:19px;display:flex;align-items:center;justify-content:center;font-size:18px;font-weight:700;text-transform:uppercase}
.base-bar{height:60px;background:var(--base);color:#ccc;font-size:12px;display:flex;align-items:center;justify-content:center}
</style>
</head>
<body>
<header class="site-header">
  <div class="wrap">
    <div class="brand"><i class="brand-mark"></i><span class="brand-name">KRV Boltmaster Group</span></div>
    <div class="top-contact">
      <span><svg width="14" height="14" viewBox="0 0 24 24"><path fill="currentColor" d="M6.6 10.8a15 15 0 006.6 6.6l2.2-2.2a1 1 0 011-.25 11.4 11.4 0 003.6.57 1 1 0 011 1V20a1 1 0 01-1 1A17 17 0 013 4a1 1 0 011-1h3.5a1 1 0 011 1c0 1.25.2 2.45.57 3.57a1 1 0 01-.25 1z"/></svg>555-014-2652</span>
      <span><svg width="16" height="13" viewBox="0 0 24 18"><path fill="currentColor" d="M0 0h24v2L12 10 0 2zM0 4l12 8 12-8v14H0z"/></svg>sales@boltmastergroup.example</span>
    </div>
  </div>
</header>

<nav class="main-nav">
  <div class="wrap">
    <ul>
      <li class="active">Home</li><li>Products</li><li>Capabilities</li><li>Engineering</li><li>Quality</li><li>About Us</li><li>Contact Us</li><li class="quote">Quote Request</li>
    </ul>
  </div>
</nav>

<section class="hero" role="img" aria-label="Photo of a yellow excavator digging earth under a blue cloudy sky">
  <div class="hero-caption"><span>Better Fasteners</span><span>For Better Products</span></div>
  <div class="hero-dots"><i></i><i></i><i class="on"></i><i></i><i></i></div>
</section>

<section class="products">
  <h2 class="section-title">Product Categories</h2>
  <div class="wrap" style="height:auto">
    <div class="product-grid">
      <article class="product"><div class="product-photo" role="img" aria-label="Photo of split lock washers" style="background:linear-gradient(135deg,#cfcfcf,#6d6a66)"></div><h3>Lock Washers</h3><p>The “Split” in the helical spring lock washer absorbs the initial driving torque and visually closes under normal bolt loading.</p><a class="more">View More &gt;</a></article>
      <article class="product"><div class="product-photo" role="img" aria-label="Photo of hitch and clevis pins" style="background:linear-gradient(135deg,#e2e2e2,#9a9a9a)"></div><h3>Pins</h3><p>The “Split” in the helical spring lock washer absorbs the initial driving torque and visually closes under normal bolt loading.</p><a class="more">View More &gt;</a></article>
      <article class="product"><div class="product-photo" role="img" aria-label="Photo of stamped tooth washers and caps" style="background:linear-gradient(135deg,#d8d8d8,#7f7f7f)"></div><h3>Stampings</h3><p>The “Split” in the helical spring lock washer absorbs the initial driving torque and visually closes under normal bolt loading.</p><a class="more">View More &gt;</a></article>
      <article class="product"><div class="product-photo" role="img" aria-label="Photo of threaded screws and bolts" style="background:linear-gradient(135deg,#e6e6e6,#8c8c8c)"></div><h3>Threaded</h3><p>The “Split” in the helical spring lock washer absorbs the initial driving torque and visually closes under normal bolt loading.</p><a class="more">View More &gt;</a></article>
    </div>
  </div>
</section>

<section class="about">
  <div class="wrap">
    <h2>About<br>KRV Boltmaster Group</h2>
    <p>The KelDrive® was created for plastic applications; the GRIP-N® as a thread forming screw, and the Meridian® for sheet metal applications. Our most recent innovation, the Boltmaster Coil®, integrates a wave thread that, in application, creates a mechanical interference ensuring the fastener simply stays tight. These threaded products are utilized in many applications in the Appliance, Trailer, Electrical, Heavy Truck and Rail markets.</p>
    <a class="btn">Read More &gt;</a>
    <div class="about-video" role="img" aria-label="Embedded product video showing assorted fasteners"></div>
  </div>
</section>

<section class="customers">
  <h2 class="section-title">Industrial Customers</h2>
  <div class="wrap" style="height:auto">
    <div class="logo-row">
      <span class="partner" style="left:192px"><i></i>HN Homeware</span>
      <span class="partner" style="left:434px"><i></i>Paul Brenner</span>
      <span class="partner" style="left:648px"><i></i>LUX</span>
      <span class="partner" style="left:856px"><i></i>Venmora</span>
    </div>
  </div>
</section>

<footer class="site-footer">
  <div class="wrap">
    <div class="foot-brand"><i class="brand-mark"></i><span class="brand-name">KRV Boltmaster Group</span></div>
    <div class="social" aria-label="Social links"><i></i><i></i><i></i><i></i></div>
    <div class="foot-col foot-contact">
      <h4>Contact Us:</h4>
      <div><svg width="14" height="14" viewBox="0 0 24 24"><path fill="currentColor" d="M6.6 10.8a15 15 0 006.6 6.6l2.2-2.2a1 1 0 011-.25 11.4 11.4 0 003.6.57 1 1 0 011 1V20a1 1 0 01-1 1A17 17 0 013 4a1 1 0 011-1h3.5a1 1 0 011 1c0 1.25.2 2.45.57 3.57a1 1 0 01-.25 1z"/></svg>555-014-2652</div>
      <div><svg width="16" height="13" viewBox="0 0 24 18"><path fill="currentColor" d="M0 0h24v2L12 10 0 2zM0 4l12 8 12-8v14H0z"/></svg>sales@boltmastergroup.example</div>
    </div>
    <div class="foot-col foot-links">
      <h4>Quick Links:</h4>
      <ul><li>Home</li><li>Products</li><li>Capabilities</li><li>Engineering</li><li>Quality</li><li>About Us</li><li>Contact Us</li></ul>
    </div>
    <div class="foot-col newsletter">
      <h4>Newsletter Signup</h4>
      <div class="field">Email Address</div>
      <div class="submit">Submit</div>
    </div>
  </div>
</footer>
<div class="base-bar">Copyright © 2017. KRV Boltmaster Group. All rights reserved.</div>
</body>
</html>
```